Bram Keystone Homes needs a business card

We need a business card for a new company in Canada, Ontario. Our company is all about luxury contraction homes for our clients. Our product and services are custom projects design. Under the business logo that will be created, we want a slogan that will be a memorable phrase for consumers to remember us to tell their friends and relatives.

Additional infomation
- Ludovic Entrasse
- President / Ceo
-519.604.3087

Find point what luxury construction products and services can be done

We like to see colors:
- #663300
- and something other colors or color that would attract the client needs and wants

The final design should communicate leads from new or old clients that will grow our empire. Most of all, we try to work among the budget that clients want

NOTE
- we also need an icon for the business (Example: Instagram, Facebook, and Whatsapp icons)
- We want the company name to be remembered easily for clients and our distributors who would get our orders.
- we need an icon on the business cards: Facebook and Instagram.

Thanks,
Bram Keystone Homes

```html
<!DOCTYPE html>
<html lang="en">
<head>
<meta charset="utf-8">
<title>Bram Keystone Homes – Business Card</title>
<link rel="stylesheet" href="https://fonts.googleapis.com/css2?family=Poppins:wght@400;500;700&family=Roboto+Condensed:wght@500&display=swap">
<style>
  :root {
    --backdrop: #2a2b2d;
    --card: #1b1c1e;
    --silver: #8c8d8f;
    --bronze: #663300;
    --bronze-light: #8a4608;
    --white: #f4f4f4;
    --divider: #9a9b9d;
  }
  * { margin: 0; padding: 0; box-sizing: border-box; }
  html, body {
    width: 1200px; height: 874px; overflow: hidden;
    background: var(--backdrop);
    font-family: "Poppins", sans-serif;
  }
  .sheet {
    width: 1200px; height: 874px;
    display: flex; flex-direction: column;
    align-items: center; justify-content: center; gap: 32px;
  }
  .card {
    width: 680px; height: 389px;
    background: var(--card);
    box-shadow: 0 10px 30px rgba(0,0,0,.45);
    position: relative;
  }
  /* Front */
  .card--front {
    display: flex; flex-direction: column; align-items: center; justify-content: center;
  }
  .brand-name {
    font-weight: 700; font-size: 44px; letter-spacing: -0.5px; line-height: 1;
  }
  .brand-name--silver { color: var(--silver); }
  .brand-name--bronze { color: var(--bronze-light); font-size: 30px; }
  .tagline {
    font-family: "Roboto Condensed", sans-serif; font-weight: 500;
    font-size: 17px; letter-spacing: .4px; margin-top: 8px; white-space: nowrap;
  }
  .tagline--silver { color: var(--silver); }
  .tagline--bronze { color: var(--bronze-light); font-size: 12px; margin-top: 6px; }
  .social-row { display: flex; gap: 4px; margin-top: 58px; }
  .social-row svg { width: 28px; height: 28px; }
  /* Back */
  .card--back {
    display: flex; align-items: center; padding: 0 0 0 60px;
  }
  .back-brand { width: 290px; text-align: center; }
  .divider {
    width: 2px; height: 110px; margin: 0 26px 0 20px;
    background: linear-gradient(to bottom, transparent, var(--divider) 25%, var(--divider) 75%, transparent);
  }
  .contact { line-height: 1.25; }
  .contact__name { color: var(--bronze-light); font-size: 22px; font-weight: 500; }
  .contact__role { color: var(--white); font-size: 19px; }
  .contact__phone { color: var(--white); font-size: 17px; font-weight: 500; }
</style>
</head>
<body>
  <main class="sheet">
    <section class="card card--front">
      <div class="brand-name brand-name--silver">Bram Keystone Homes</div>
      <div class="tagline tagline--silver">- HOME RENOVATIONS - CUSTOM PROJECT DESIGN -</div>
      <div class="social-row" aria-label="Social media">
        <svg viewBox="0 0 28 28"><circle cx="14" cy="14" r="12.5" fill="none" stroke="var(--bronze)" stroke-width="1.6"/></svg>
        <svg viewBox="0 0 28 28"><circle cx="14" cy="14" r="12.5" fill="none" stroke="var(--bronze)" stroke-width="1.6"/></svg>
        <svg viewBox="0 0 28 28"><circle cx="14" cy="14" r="12.5" fill="none" stroke="var(--bronze)" stroke-width="1.6"/></svg>
      </div>
    </section>

    <section class="card card--back">
      <div class="back-brand">
        <div class="brand-name brand-name--bronze">Bram Keystone Homes</div>
        <div class="tagline tagline--bronze">- HOME RENOVATIONS - CUSTOM PROJECT DESIGN -</div>
      </div>
      <div class="divider"></div>
      <div class="contact">
        <div class="contact__name">Ludovic Entrasse</div>
        <div class="contact__role">President / Ceo</div>
        <div class="contact__phone">519.604.3087</div>
      </div>
    </section>
  </main>
</body>
</html>
```